Redesign of business card for Cedar Ridge Mechanical

We are looking for a new design for our business cards for Cedar Ridge Mechanical. We are a plumbing & HVAC construction company, operating on the West Coast of Canada and USA. Logo attached.
Industry/Entity Type
Construction - Plumbing & HVAC
Contact Information for Business Card
Name, address, phone numbers, email, website address
Look and feel
Each slider illustrates characteristics of the customer's brand and the style your logo design should communicate.

```html
<!DOCTYPE html>
<html lang="en">
<head>
<meta charset="utf-8">
<title>Cedar Ridge Mechanical – Business Card</title>
<link href="https://fonts.googleapis.com/css2?family=Montserrat:wght@400;700&family=Oswald:wght@500&display=swap" rel="stylesheet">
<style>
  :root {
    --backdrop: #1d1d1f;
    --card-light: #ffffff;
    --card-dark: #121212;
    --card-dark-panel: #1a1a1a;
    --ink: #1a1a1a;
    --ink-soft: #6d6d6d;
    --rule: #8a8a8a;
    --steel: #8c8c8c;
  }
  * { box-sizing: border-box; margin: 0; padding: 0; }
  html, body { width: 1200px; height: 801px; overflow: hidden; }
  body {
    background: var(--backdrop);
    font-family: "Montserrat", sans-serif;
    position: relative;
  }
  .card {
    position: absolute;
    top: 252px;
    width: 520px;
    height: 297px;
    border-radius: 18px;
    overflow: hidden;
  }
  .card--front { left: 50px; background: var(--card-light); color: var(--ink); }
  .card--back { left: 630px; background: var(--card-dark); }

  .front__brand {
    position: absolute; top: 34px; right: 34px;
    display: flex; align-items: center; gap: 10px;
    font-family: "Oswald", sans-serif; font-weight: 500;
    font-size: 17px; letter-spacing: 1.5px; text-transform: uppercase;
    color: var(--ink);
  }
  .front__brand-mark { width: 26px; height: 26px; background: var(--ink); border-radius: 3px; }
  .front__divider {
    position: absolute; left: 34px; right: 34px; top: 148px;
    border-top: 1px solid var(--rule);
  }
  .front__address {
    position: absolute; right: 34px; top: 90px; text-align: right;
    font-size: 13px; line-height: 1.4; color: var(--ink-soft);
  }
  .front__person { position: absolute; left: 34px; top: 166px; }
  .person__name { font-size: 19px; font-weight: 700; letter-spacing: 0.5px; }
  .person__name span { color: var(--ink-soft); }
  .person__role { font-size: 13px; color: var(--ink-soft); margin-top: 2px; }
  .person__rule { width: 220px; border-top: 1px solid var(--rule); margin: 10px 0 8px; }
  .contact { list-style: none; font-size: 13px; color: var(--ink-soft); }
  .contact li { display: flex; align-items: center; gap: 8px; line-height: 1.55; }
  .contact svg { width: 11px; height: 11px; fill: var(--ink); flex: none; }

  .back__panel {
    position: absolute; inset: 22px 26px;
    border-radius: 12px; background: var(--card-dark-panel);
    border: 10px solid #2a2a2a;
  }
  .back__name {
    position: absolute; left: 0; right: 0; top: 50%; transform: translateY(-50%);
    text-align: center;
    font-family: "Oswald", sans-serif; font-weight: 500;
    font-size: 34px; letter-spacing: 3px; text-transform: uppercase;
    color: var(--steel);
  }
</style>
</head>
<body>
  <section class="card card--front" aria-label="Business card front">
    <div class="front__brand"><span class="front__brand-mark"></span>Cedar Ridge Mechanical</div>
    <p class="front__address">Your address, city<br>state, ZIP 0000</p>
    <div class="front__divider"></div>
    <div class="front__person">
      <h1 class="person__name">DANIEL <span>BROOKS</span></h1>
      <p class="person__role">Manager</p>
      <div class="person__rule"></div>
      <ul class="contact">
        <li><svg viewBox="0 0 24 24"><path d="M6.6 10.8a15 15 0 0 0 6.6 6.6l2.2-2.2a1 1 0 0 1 1-.25 11 11 0 0 0 3.6.6 1 1 0 0 1 1 1V20a1 1 0 0 1-1 1A17 17 0 0 1 3 4a1 1 0 0 1 1-1h3.5a1 1 0 0 1 1 1c0 1.25.2 2.45.6 3.6a1 1 0 0 1-.25 1z"/></svg>123-456-2100</li>
        <li><svg viewBox="0 0 24 24"><path d="M2 5h20v14H2zm2 2v.5l8 5 8-5V7z"/></svg>youremail@mailbox.com</li>
        <li><svg viewBox="0 0 24 24"><circle cx="12" cy="12" r="10"/></svg>www.yourwebsite.com</li>
      </ul>
    </div>
  </section>

  <section class="card card--back" aria-label="Business card back">
    <div class="back__panel"></div>
    <p class="back__name">Cedar Ridge Mechanical</p>
  </section>
</body>
</html>
```